Investment Advisor E-Newsletter Banner Design

I need a banner designed for an email newsletter that will be sent monthly to clients and prospects. We want to see designs that are elegant and use our logo well. The banner should be 922x150px and should go well with the www.tlvbanda.com website. Should include Logo and email and phone number.

Target Market(s)

High net worth investors

Number of Pages Required

1 page

Requirements
Must have
• logo, place for email (info@tlvbanda.com) and phone number (415-297-6180), colors and design that work well with www.tlvbanda.com website

```html
<!DOCTYPE html>
<html lang="en">
<head>
<meta charset="utf-8">
<title>Tolvan Capital – Newsletter Banners</title>
<link rel="stylesheet" href="https://fonts.googleapis.com/css2?family=Noto+Serif:wght@400;700&display=swap">
<style>
  :root {
    --stage: #0d1113;
    --stage-glow: #1a2024;
    --banner-bg: #f0f0f0;
    --banner-frame: #ffffff;
    --navy: #2c2f80;
    --ink: #333333;
    --arc-grey: #5f5f61;
    --arc-purple: #7a76bd;
  }
  * { margin: 0; padding: 0; box-sizing: border-box; }
  html, body { width: 1200px; height: 671px; overflow: hidden; }
  body {
    background: radial-gradient(ellipse at 50% 45%, var(--stage-glow) 0%, var(--stage) 70%);
    font-family: "Noto Serif", Georgia, serif;
    position: relative;
  }
  .banner {
    position: absolute;
    left: 162px;
    width: 877px;
    height: 146px;
    background: var(--banner-bg);
    border: 3px solid var(--banner-frame);
    border-radius: 3px;
    overflow: hidden;
  }
  .banner--tagline { top: 166px; }
  .banner--contact { top: 365px; }

  .brand { position: absolute; display: flex; align-items: center; gap: 10px; }
  .brand__mark { width: 58px; height: 58px; border-radius: 50%; background: var(--navy); flex: none; }
  .brand__name { color: var(--navy); font-weight: 400; line-height: 1.1; }
  .brand__name-main { display: block; font-size: 30px; }
  .brand__name-sub { display: block; font-size: 14.5px; margin-top: 4px; }
  .banner--tagline .brand { left: 42px; top: 22px; }
  .banner--contact .brand { left: 44px; top: 40px; }

  .tagline { position: absolute; left: 358px; top: 14px; text-align: center; }
  .tagline__lead { display: block; color: var(--navy); font-size: 22px; font-weight: 400; }
  .tagline__main { display: block; color: var(--ink); font-size: 36px; font-weight: 700; line-height: 1.05; }

  .contact { position: absolute; display: flex; align-items: center; gap: 14px; color: var(--navy); font-weight: 700; }
  .contact svg { flex: none; fill: var(--navy); }
  .banner--tagline .contact { top: 106px; font-size: 18px; }
  .banner--tagline .contact--phone { left: 93px; }
  .banner--tagline .contact--email { left: 302px; }
  .banner--contact .contact { font-size: 20px; left: 351px; }
  .banner--contact .contact--phone { top: 39px; }
  .banner--contact .contact--email { top: 82px; }

  .photo-arc { position: absolute; inset: 0; width: 100%; height: 100%; }
</style>
</head>
<body>

  <section class="banner banner--tagline">
    <svg class="photo-arc" viewBox="0 0 871 140" preserveAspectRatio="none" aria-hidden="false">
      <defs>
        <linearGradient id="deskTones" x1="0" y1="0" x2="1" y2="1">
          <stop offset="0" stop-color="#c89a6a"/>
          <stop offset="0.45" stop-color="#e6ddd2"/>
          <stop offset="1" stop-color="#8a6a52"/>
        </linearGradient>
      </defs>
      <path d="M634,0 C640,70 700,130 790,140 L871,140 L871,0 Z" fill="var(--arc-grey)"/>
      <path d="M642,0 C650,66 708,124 800,140 L871,140 L871,0 Z" fill="var(--arc-purple)"/>
      <path d="M648,0 C658,62 716,120 810,140 L871,140 L871,0 Z" fill="url(#deskTones)" role="img" aria-label="Photo of hands reviewing financial charts on a desk"/>
    </svg>

    <div class="brand">
      <span class="brand__mark"></span>
      <span class="brand__name">
        <span class="brand__name-main">Tolvan Capital</span>
        <span class="brand__name-sub">Management &amp; Research, Inc.</span>
      </span>
    </div>

    <h1 class="tagline">
      <span class="tagline__lead">Evidence-Based</span>
      <span class="tagline__main">Investing</span>
    </h1>

    <p class="contact contact--phone">
      <svg width="18" height="18" viewBox="0 0 24 24"><path d="M6.6 10.8a15.1 15.1 0 0 0 6.6 6.6l2.2-2.2a1 1 0 0 1 1-.25 11.4 11.4 0 0 0 3.6.57 1 1 0 0 1 1 1V20a1 1 0 0 1-1 1A17 17 0 0 1 3 4a1 1 0 0 1 1-1h3.5a1 1 0 0 1 1 1c0 1.25.2 2.45.57 3.57a1 1 0 0 1-.25 1z"/></svg>
      Call 415-297-6180
    </p>
    <p class="contact contact--email">
      <svg width="18" height="14" viewBox="0 0 18 14"><rect width="18" height="14" rx="1"/><path d="M1 1.5 9 8l8-6.5" stroke="#f0f0f0" stroke-width="1.6" fill="none"/></svg>
      info@tlvbanda.com
    </p>
  </section>

  <section class="banner banner--contact">
    <svg class="photo-arc" viewBox="0 0 871 140" preserveAspectRatio="none">
      <defs>
        <linearGradient id="tabletTones" x1="0" y1="0" x2="1" y2="1">
          <stop offset="0" stop-color="#2e5c8c"/>
          <stop offset="0.5" stop-color="#6f9cc6"/>
          <stop offset="1" stop-color="#1d3f66"/>
        </linearGradient>
      </defs>
      <path d="M634,0 C640,70 700,130 790,140 L871,140 L871,0 Z" fill="var(--arc-grey)"/>
      <path d="M642,0 C650,66 708,124 800,140 L871,140 L871,0 Z" fill="var(--arc-purple)"/>
      <path d="M648,0 C658,62 716,120 810,140 L871,140 L871,0 Z" fill="url(#tabletTones)" role="img" aria-label="Photo of a businessman holding a tablet with market charts"/>
    </svg>

    <div class="brand">
      <span class="brand__mark"></span>
      <span class="brand__name">
        <span class="brand__name-main">Tolvan Capital</span>
        <span class="brand__name-sub">Management &amp; Research, Inc.</span>
      </span>
    </div>

    <p class="contact contact--phone">
      <svg width="20" height="20" viewBox="0 0 24 24"><path d="M6.6 10.8a15.1 15.1 0 0 0 6.6 6.6l2.2-2.2a1 1 0 0 1 1-.25 11.4 11.4 0 0 0 3.6.57 1 1 0 0 1 1 1V20a1 1 0 0 1-1 1A17 17 0 0 1 3 4a1 1 0 0 1 1-1h3.5a1 1 0 0 1 1 1c0 1.25.2 2.45.57 3.57a1 1 0 0 1-.25 1z"/></svg>
      Call 415-297-6180
    </p>
    <p class="contact contact--email">
      <svg width="19" height="15" viewBox="0 0 18 14"><rect width="18" height="14" rx="1"/><path d="M1 1.5 9 8l8-6.5" stroke="#f0f0f0" stroke-width="1.6" fill="none"/></svg>
      info@tlvbanda.com
    </p>
  </section>

</body>
</html>
```